Support People to improve their image and well-being by provided personalised advise

We need a design for business cards that could be used for production on plano press. We build a new business in our region for advising mostly women (also men though) on style embracing several aspects including fashion, style, self-confidence and ultimately your internal and external image. The business card should be "classy", "french-style". The business is located in the french -speaking part of Switzerland, close to France. The name of the company is Lomu Grace

Target Market(s)

Service fees won't be cheap (medium to premium) thus we target mid-class to upper-class women (1st target) and men (2nd target)

Industry/Entity Type

Life Coaching

Contact Information for Business Card

Conseil en Image

+41 76 418 63 07
tovasel@lomu-grace.example
profil.example/in/sel-moran-tova

Logo Text

Lomu Grace

Colors

Designer to choose colors to be used in the design.

```html
<!DOCTYPE html>
<html lang="fr">
<head>
<meta charset="utf-8">
<title>Lomu Grace – Cartes de visite</title>
<link rel="stylesheet" href="https://fonts.googleapis.com/css2?family=Lato:wght@400;700&display=swap">
<style>
  :root {
    --canvas-bg: #ecebee;
    --card-white: #ffffff;
    --plum: #721c6f;
    --plum-bright: #a4249f;
    --plum-deep: #5e1a5c;
    --night: #161616;
    --rule-grey: #8a8a8a;
    --text-grey: #b9b9b9;
    --badge-blue: #1b78b8;
    --ink-white: #ffffff;
  }
  * { margin: 0; padding: 0; box-sizing: border-box; }
  html, body { width: 1200px; height: 900px; overflow: hidden; }
  body {
    background: var(--canvas-bg);
    font-family: "Lato", Arial, sans-serif;
    position: relative;
  }
  .card {
    position: absolute;
    overflow: hidden;
    box-shadow: 0 6px 18px rgba(0,0,0,0.18);
  }

  /* Front card */
  .card--front {
    left: 178px; top: 75px;
    width: 588px; height: 362px;
    background: var(--card-white);
  }
  .front__wordmark {
    position: absolute;
    left: 0; right: 0; top: 72px;
    text-align: center;
    font-weight: 400;
    font-size: 56px;
    letter-spacing: 1px;
    color: var(--plum);
  }
  .front__band {
    position: absolute;
    left: 0; right: 0; top: 200px; bottom: 0;
    background: var(--plum);
  }
  .front__squares {
    position: absolute;
    left: 0; top: 200px;
    width: 340px; height: 40px;
    background: var(--card-white);
    padding: 3px 4px 5px 0;
  }
  .front__squares-fill {
    width: 100%; height: 100%;
    background: linear-gradient(90deg, var(--plum-deep), var(--plum-bright), var(--plum-deep), var(--plum-bright));
  }
  .front__contact {
    position: absolute;
    left: 30px; top: 278px;
    color: var(--ink-white);
    font-size: 16px;
    line-height: 23px;
  }
  .contact__line { display: flex; align-items: center; gap: 5px; }
  .contact__icon { width: 13px; height: 13px; fill: var(--ink-white); }
  .front__person {
    position: absolute;
    right: 35px; top: 272px;
    text-align: right;
    color: var(--ink-white);
  }
  .person__name { font-weight: 700; font-size: 21px; letter-spacing: 0.2px; }
  .person__role { font-size: 16px; margin-top: 1px; }

  /* Back card */
  .card--back {
    left: 388px; top: 505px;
    width: 567px; height: 352px;
    background: var(--night);
  }
  .back__wordmark {
    position: absolute;
    left: 0; right: 0; top: 112px;
    text-align: center;
    font-weight: 400;
    font-size: 50px;
    letter-spacing: 1px;
    color: var(--plum-bright);
  }
  .back__divider {
    position: absolute;
    left: 145px; top: 236px;
    width: 277px; height: 28px;
  }
  .back__profile {
    position: absolute;
    left: 0; right: 0; top: 271px;
    text-align: center;
    font-size: 18px;
    color: var(--text-grey);
    letter-spacing: 0.2px;
  }
</style>
</head>
<body>

  <section class="card card--front" aria-label="Recto de la carte">
    <div class="front__wordmark">Lomu Grace</div>
    <div class="front__band"></div>
    <div class="front__squares">
      <div class="front__squares-fill" role="img" aria-label="Row of alternating purple squares"></div>
    </div>
    <div class="front__contact">
      <div class="contact__line">
        <svg class="contact__icon" viewBox="0 0 16 16" aria-hidden="true">
          <path d="M2 5c0-2 2-3 6-3s6 1 6 3v1h-3V5H5v1H2z M4 7h8l2 6H2z"/>
        </svg>
        <span>+41 76 418 63 07</span>
      </div>
      <div class="contact__line">
        <svg class="contact__icon" viewBox="0 0 16 16" aria-hidden="true">
          <path d="M1 3h14v10H1z" fill="#fff"/>
          <path d="M1 3l7 6 7-6" fill="none" stroke="#721c6f" stroke-width="1.5"/>
        </svg>
        <span>tovasel@lomu-grace.example</span>
      </div>
    </div>
    <div class="front__person">
      <div class="person__name">ADRIEN VALLET</div>
      <div class="person__role">Managing Director</div>
    </div>
  </section>

  <section class="card card--back" aria-label="Verso de la carte">
    <div class="back__wordmark">Lomu Grace</div>
    <svg class="back__divider" viewBox="0 0 277 28" aria-hidden="true">
      <line x1="0" y1="14" x2="122" y2="14" stroke="var(--rule-grey)" stroke-width="1"/>
      <circle cx="138.5" cy="14" r="13" fill="var(--badge-blue)"/>
      <line x1="155" y1="14" x2="277" y2="14" stroke="var(--rule-grey)" stroke-width="1"/>
    </svg>
    <div class="back__profile">profil.example/in/sel-moran-tova</div>
  </section>

</body>
</html>
```